Wren Arts Competition Event For Teenagers Needs Promo Graphics

I am in need of graphics for 2019 Prairie Wren Arts Showcase. It is a Wren Arts competition event for teenagers. I need graphics to make an 11x17 poster and a main title graphic that I can use for digital (social, 16x9 for screens, etc). Graphic should include the following 2 logos: the KM Rising Tide logo (this is who we are) and the "circles" logo is the logo of Wren Arts Showcase so that can be incorporated but is not mandatory and does not need to be in color. Tag line for Wren Arts is "Discover. Develop. Deploy." Again, this is optional. Looking for an artistic design - geometric shapes, bright colors, or something along those lines. Something that speaks to teenagers and especially creatives/Wren Arts types. Additionally, Post should include:
Harbor Lane Chapel
March 29-30
(registration & cost info may be added to the poster before design is finalized; still working on those details)

```html
<!DOCTYPE html>
<html lang="en">
<head>
<meta charset="utf-8">
<title>2019 Prairie Wren Arts Showcase – Poster</title>
<link rel="stylesheet" href="https://fonts.googleapis.com/css2?family=Russo+One&family=Saira+Condensed:wght@700;800&display=swap">
<style>
  :root {
    --stage: #e9e8e6;
    --ink: #0b0b0d;
    --white: #ffffff;
    --cyan: #12a9e0;
    --blue: #1f7fb6;
    --navy: #2a3a8c;
    --purple: #6d3a96;
    --magenta: #e2266f;
    --orange: #f7941d;
    --yellow: #ffd200;
    --grey: #cfcfcf;
  }
  html, body {
    margin: 0;
    padding: 0;
    width: 1200px;
    height: 726px;
    overflow: hidden;
    background: var(--stage);
  }
  .stage {
    position: relative;
    width: 1200px;
    height: 726px;
  }
  .poster {
    position: absolute;
    left: 357px;
    top: 18px;
    width: 486px;
    height: 690px;
    display: block;
    box-shadow: 0 6px 18px rgba(0,0,0,.18);
  }
  .title { font-family: "Russo One", "Arial Black", sans-serif; }
  .title-shadow { fill: var(--purple); }
  .title-face { fill: var(--white); }
  .band-text {
    font-family: "Russo One", "Arial Black", sans-serif;
    fill: var(--ink);
  }
  .info { font-family: "Saira Condensed", "Arial Narrow", sans-serif; font-weight: 800; }
  .info-white { fill: var(--white); }
  .info-yellow { fill: var(--yellow); }
  .venue-text {
    font-family: "Saira Condensed", "Arial Narrow", sans-serif;
    font-weight: 800;
    fill: var(--ink);
  }
  .sponsor-name {
    font-family: "Saira Condensed", "Arial Narrow", sans-serif;
    font-weight: 800;
  }
  .sponsor-showcase { fill: var(--white); }
  .sponsor-host { fill: var(--cyan); }
</style>
</head>
<body>
<main class="stage">
  <svg class="poster" viewBox="0 0 640 908" xmlns="http://www.w3.org/2000/svg" aria-labelledby="poster-title">
    <title id="poster-title">2019 Prairie Wren Arts Showcase poster</title>
    <defs>
      <linearGradient id="grad-band" x1="0" x2="1" y1="0" y2="0">
        <stop offset="0" stop-color="var(--cyan)"/>
        <stop offset="0.5" stop-color="#8a7db8"/>
        <stop offset="1" stop-color="var(--magenta)"/>
      </linearGradient>
      <linearGradient id="grad-info" x1="0" x2="1" y1="0" y2="0">
        <stop offset="0" stop-color="var(--purple)"/>
        <stop offset="1" stop-color="var(--magenta)"/>
      </linearGradient>
      <linearGradient id="grad-date" x1="0" x2="1" y1="0" y2="0">
        <stop offset="0" stop-color="var(--blue)"/>
        <stop offset="1" stop-color="#1a95c9"/>
      </linearGradient>
      <linearGradient id="grad-venue" x1="0" x2="1" y1="0" y2="0">
        <stop offset="0" stop-color="var(--navy)"/>
        <stop offset="0.5" stop-color="var(--purple)"/>
        <stop offset="1" stop-color="var(--magenta)"/>
      </linearGradient>
      <linearGradient id="grad-artwork" x1="0" x2="0.6" y1="0" y2="1">
        <stop offset="0" stop-color="var(--orange)"/>
        <stop offset="0.5" stop-color="var(--magenta)"/>
        <stop offset="1" stop-color="var(--purple)"/>
      </linearGradient>
      <linearGradient id="grad-corner" x1="0" x2="1" y1="0" y2="1">
        <stop offset="0" stop-color="var(--orange)"/>
        <stop offset="1" stop-color="var(--cyan)"/>
      </linearGradient>
    </defs>

    <rect class="backdrop" width="640" height="908" fill="var(--ink)"/>
    <rect class="artwork" x="0" y="370" width="320" height="538" fill="url(#grad-artwork)" role="img" aria-label="Bright gradient geometric triangle artwork"/>
    <rect class="artwork" x="520" y="0" width="120" height="120" fill="url(#grad-corner)" opacity=".85" role="img" aria-label="Corner geometric triangle artwork"/>

    <g class="title">
      <text class="title-shadow" x="51" y="149" font-size="82" textLength="545" lengthAdjust="spacingAndGlyphs">2019 PRAIRIE</text>
      <text class="title-face" x="46" y="144" font-size="82" textLength="545" lengthAdjust="spacingAndGlyphs">2019 PRAIRIE</text>
      <text class="title-shadow" x="51" y="275" font-size="148" textLength="550" lengthAdjust="spacingAndGlyphs">WREN</text>
      <text class="title-face" x="44" y="269" font-size="148" textLength="550" lengthAdjust="spacingAndGlyphs">WREN</text>
    </g>
    <rect x="42" y="285" width="558" height="73" fill="url(#grad-band)"/>
    <text class="band-text" x="56" y="342" font-size="48" textLength="530" lengthAdjust="spacingAndGlyphs">WREN ARTS SHOWCASE</text>

    <g class="sponsors">
      <circle cx="318" cy="440" r="20" fill="none" stroke="var(--grey)" stroke-width="5"/>
      <text class="sponsor-name sponsor-showcase" x="348" y="449" font-size="26">WREN ARTS</text>
      <text class="sponsor-name sponsor-host" x="600" y="432" font-size="38" text-anchor="end">KM RISING</text>
      <text class="sponsor-name sponsor-host" x="600" y="470" font-size="38" text-anchor="end">TIDE</text>
    </g>

    <rect x="310" y="530" width="330" height="135" fill="url(#grad-info)"/>
    <g class="info">
      <text class="info-white" x="382" y="562" font-size="28">FOR MORE</text>
      <text class="info-yellow" x="382" y="592" font-size="34">INFORMATION</text>
      <text class="info-white" x="382" y="620" font-size="28">AND TO REGISTER</text>
      <text class="info-white" x="382" y="652" font-size="34">BY MARCH 7TH</text>
    </g>

    <rect x="380" y="675" width="260" height="105" fill="url(#grad-date)"/>
    <g class="info">
      <text class="info-white" x="432" y="716" font-size="36">MARCH</text>
      <line x1="432" y1="726" x2="550" y2="726" stroke="var(--white)" stroke-width="2"/>
      <text class="info-white" x="432" y="764" font-size="36">29–30</text>
    </g>

    <circle cx="283" cy="727" r="116" fill="url(#grad-venue)"/>
    <g class="venue-text" text-anchor="middle">
      <text x="283" y="697" font-size="52">HARBOR</text>
      <text x="283" y="746" font-size="52">LANE</text>
      <text x="283" y="795" font-size="52">CHAPEL</text>
    </g>

    <g class="info" text-anchor="middle">
      <text class="info-yellow" x="492" y="845" font-size="42">VISIT</text>
      <text class="info-white" x="492" y="875" font-size="28">KMRISINGTIDE.COM</text>
    </g>
  </svg>
</main>
</body>
</html>
```